Elegant, High End Integrated Wellness Healthcare Practice

We need a brochure designed for an integrated mind-body wellness healthcare practice (www.quellarivecare.com) . This brochure will be used when we cold call prospects (physicians to refer to our office, and potential consumers to utilize our services). Our practice is geographically located in the middle Tennessee USA region, although we have plans to become an international company as many of our offerings can be accessed anywhere in the world. Ultimately our goal is to have this brochure used as a leave-behind in an effort to introduce our integrated offerings to increase market share. The final product brochure should be both elegant and serious, with clean lines but also convey warmth and trust, as individuals who are coming for our services have usually struggled with their health for a significant amount of time before finding our practice.
Updates

The design brief was very specific about providing a high-end science-based 2-page brochure (not flier). Several designs submitted were fliers. The other designs were heavy on yoga or "woo woo" non-science-based looking pictures. This is a flier to appeal to physicians and other healthcare providers. Therefore the design must speak science and evidence-based methods of mind and body wellness care. I would also like to appeal to the other designers I paid extra for their submissions and who have indicated they will "respond in the coming days."

```html
<!DOCTYPE html>
<html lang="en">
<head>
<meta charset="utf-8">
<title>What We Do – Quellarive Care</title>
<link href="https://fonts.googleapis.com/css2?family=Cinzel:wght@500;700&family=Roboto:wght@300;400&display=swap" rel="stylesheet">
<style>
  :root {
    --forest: #1f3a0b;
    --leaf: #72ab3b;
    --body-text: #666666;
    --paper: #ffffff;
    --photo-light: #efe9dc;
    --photo-warm: #c7a775;
    --photo-green: #9aa668;
  }
  * { margin: 0; padding: 0; box-sizing: border-box; }
  html, body { width: 927px; height: 1200px; overflow: hidden; background: var(--paper); }
  .page { position: relative; width: 927px; height: 1200px; overflow: hidden; background: var(--paper); }

  .hero-photo {
    position: absolute; left: -132px; top: -93px; width: 648px; height: 648px; border-radius: 50%;
    background: radial-gradient(circle at 55% 40%, var(--photo-light) 0%, #e3d6bb 40%, var(--photo-warm) 70%, var(--photo-green) 100%);
  }
  .arc-band { position: absolute; left: 0; top: 0; }

  .page-title {
    position: absolute; right: 40px; top: 44px;
    font-family: "Cinzel", serif; font-weight: 500; font-size: 62px; line-height: 1;
    color: var(--forest); font-variant: small-caps; letter-spacing: 1px;
  }

  .service { position: absolute; }
  .service h2 {
    font-family: "Cinzel", serif; font-weight: 700; font-size: 19px; line-height: 1;
    color: var(--forest); letter-spacing: 0.5px; margin-bottom: 19px;
  }
  .service p {
    font-family: "Roboto", sans-serif; font-weight: 300; font-size: 12.7px; line-height: 19px;
    color: var(--body-text);
  }
  .service.right { right: 113px; text-align: right; }
  .service.left { left: 391px; text-align: left; }

  .badge { position: absolute; width: 54px; height: 54px; }
  .badge span {
    position: absolute; inset: 0; display: flex; align-items: center; justify-content: center;
    font-family: "Cinzel", serif; font-weight: 700; font-size: 19px; color: var(--forest);
  }
  .badge svg { position: absolute; inset: 0; }

  .brand { position: absolute; left: 20px; top: 1072px; display: flex; align-items: center; gap: 20px; }
  .brand-dot { width: 120px; height: 120px; border-radius: 50%; background: var(--leaf); }
  .brand-name {
    font-family: "Cinzel", serif; font-weight: 700; font-size: 40px; line-height: 1.5;
    color: var(--forest);
  }
</style>
</head>
<body>
<div class="page">
  <div class="hero-photo" role="img" aria-label="Photograph of a woman breathing deeply outdoors in soft morning light"></div>

  <svg class="arc-band" width="927" height="1200" viewBox="0 0 927 1200" aria-hidden="true">
    <path d="M689,247 C400,250 128,520 128,774 C128,900 170,1000 217,1065 L283,1065 C230,990 196,890 196,774 C196,560 380,300 689,247 Z" fill="var(--leaf)"/>
  </svg>

  <h1 class="page-title">What We Do</h1>

  <section class="service right" style="top:325px; width:360px;">
    <h2>An Integrative Approach</h2>
    <p>Join us in our mission to change healthcare as we know it. Guided step-by-step by our care team, well embark on an integrative approach to cover more of the issues we face across the lifespan.</p>
  </section>
  <div class="badge" style="left:832px; top:321px;">
    <svg viewBox="0 0 54 54"><path d="M27,3 A24,24 0 0 1 51,27" fill="none" stroke="var(--leaf)" stroke-width="4"/><path d="M51,27 A24,24 0 1 1 27,3" fill="none" stroke="var(--forest)" stroke-width="3"/></svg>
    <span>01</span>
  </div>

  <section class="service left" style="top:490px; width:335px;">
    <h2>Personalized Care</h2>
    <p>This is no “one-size-fits-all” when it comes to giving yourself the best care. Everyone is biologically unique, and as we age, we have different needs and requirements.</p>
  </section>
  <div class="badge" style="left:322px; top:486px;">
    <svg viewBox="0 0 54 54"><path d="M27,3 A24,24 0 0 1 51,27" fill="none" stroke="var(--leaf)" stroke-width="4"/><path d="M51,27 A24,24 0 1 1 27,3" fill="none" stroke="var(--forest)" stroke-width="3"/></svg>
    <span>02</span>
  </div>

  <section class="service right" style="top:662px; width:360px;">
    <h2>Innovative Treatments</h2>
    <p>Did you know that it takes on average 17 years for clinical breakthroughs to make their way into your conventional doctor’s office?</p>
  </section>
  <div class="badge" style="left:832px; top:658px;">
    <svg viewBox="0 0 54 54"><path d="M27,3 A24,24 0 0 1 51,27" fill="none" stroke="var(--leaf)" stroke-width="4"/><path d="M51,27 A24,24 0 1 1 27,3" fill="none" stroke="var(--forest)" stroke-width="3"/></svg>
    <span>03</span>
  </div>

  <section class="service left" style="top:826px; width:335px;">
    <h2>Root Cause Resolution</h2>
    <p>We get to the bottom of WHY you feel sluggish, depressed, anxious, distracted, can’t release stubborn weight, or struggle with brain fog.</p>
  </section>
  <div class="badge" style="left:322px; top:822px;">
    <svg viewBox="0 0 54 54"><path d="M27,3 A24,24 0 0 1 51,27" fill="none" stroke="var(--leaf)" stroke-width="4"/><path d="M51,27 A24,24 0 1 1 27,3" fill="none" stroke="var(--forest)" stroke-width="3"/></svg>
    <span>04</span>
  </div>

  <section class="service right" style="top:984px; width:360px;">
    <h2>Co-Creating Health</h2>
    <p>Changing your lifestyle may seem daunting, but we also equip you with mindset tools &amp; mentorship to overcome life habits that are an impediment to optimal wellness.</p>
  </section>
  <div class="badge" style="left:832px; top:980px;">
    <svg viewBox="0 0 54 54"><path d="M27,3 A24,24 0 0 1 51,27" fill="none" stroke="var(--leaf)" stroke-width="4"/><path d="M51,27 A24,24 0 1 1 27,3" fill="none" stroke="var(--forest)" stroke-width="3"/></svg>
    <span>05</span>
  </div>

  <div class="brand">
    <div class="brand-dot" aria-hidden="true"></div>
    <div class="brand-name">Quellarive<br>Care</div>
  </div>
</div>
</body>
</html>
```